Valdane Companies Business Card Design

We need a new business card for our Private Equity Real Estate Development firm, “Valdane” and our EB-5 regional center “Thornmere Regional Center” on one card. We prefer a design that is simple, elegant, and represents the luxury products we design and build as well as the financial security and stability our successful history has produced. We are an industry leader in our field and 3rd generation family business that has evolved into an institutional quality investment platform. Considered design size is standard business card dimensions (3.5 x 2 inches with an additional 1/8 inch space for design elements or backgrounds that extend beyond the finished size of your piece.

Target Market(s)

• High net worth individuals
• Highly skilled technical workers and physicians in the US seeking investment-based immigration opportunities
• Sophisticated private equity investors
• Intermediary partners include domestic attorneys and investment brokers, as well as international agent networks
• US real estate developers

Industry/Entity Type

Finance

Contact Information for Business Card

(Providing placeholder info for personal information, please design for longer character spaces, longer names and addresses etc..)
• Logo for Valdane
• Logo for Thornmere Regional Center
• Full name: Marcus Valdane
• Job title: CEO
• Email address: mvaldane@valdanecompanies.com
• Cell phone number: +1.555.314.2287
• Office number +1.555.628.4410
• Office address: Larkfield Court 5, 4817 Vista Orilla, San Ramon, CA.
• Website: www.valdanecompanies.com

Font styles to use
Serif
Sans Serif

Colors
ec1f27
ffffff
000000

Requirements
Must have
• • Logo for Valdane
• • Logo for Thornmere Regional Center
• - Use rounded corners
• (See .ai file included for logos)
Nice to have
• • Simple, elegant design
• • Aesthetically compatible with our website design (www.valdanecompanies.com)
• • Color palette including but not limited to white, black, and red (as per logos)
Should not have
• - Not too much red color
• - Do not stack both logos on top of each other

```html
<!DOCTYPE html>
<html lang="en">
<head>
<meta charset="utf-8">
<title>Valdane Companies Business Card</title>
<link href="https://fonts.googleapis.com/css2?family=Roboto:wght@400;500&display=swap" rel="stylesheet">
<style>
  :root {
    --backdrop: #2b2b2d;
    --card: #262527;
    --ink: #ffffff;
    --ink-soft: #e6e6e6;
    --mark: #bdbdbd;
  }
  html, body {
    margin: 0;
    padding: 0;
    width: 1200px;
    height: 1200px;
    overflow: hidden;
    background: var(--backdrop);
    font-family: "Roboto", Arial, sans-serif;
    color: var(--ink);
  }
  .canvas { position: relative; width: 1200px; height: 1200px; }
  .card {
    position: absolute;
    left: 194px;
    width: 878px;
    height: 502px;
    border-radius: 26px;
    background: var(--card);
  }
  .card--front { top: 34px; }
  .card--back { top: 664px; }

  .brand {
    position: absolute;
    display: flex;
    align-items: center;
    gap: 16px;
    font-weight: 500;
    font-size: 40px;
    line-height: 48px;
    letter-spacing: 1px;
    color: var(--ink);
    white-space: nowrap;
  }
  .brand__square {
    width: 48px;
    height: 48px;
    background: var(--mark);
    flex: none;
  }
  .card--front .brand { right: 36px; top: 106px; }
  .card--back .brand { right: 50px; top: 368px; font-size: 34px; }

  .person__name,
  .person__title,
  .person__address,
  .contacts {
    position: absolute;
    left: 38px;
    margin: 0;
    white-space: nowrap;
  }
  .person__name { top: 208px; font-size: 36px; line-height: 40px; font-weight: 500; }
  .person__title { top: 253px; left: 39px; font-size: 21px; line-height: 24px; color: var(--ink-soft); }
  .person__address { top: 297px; left: 39px; font-size: 20px; line-height: 22px; color: var(--ink-soft); }

  .contacts {
    top: 359px;
    padding: 0;
    list-style: none;
    font-size: 19px;
    color: var(--ink-soft);
  }
  .contacts li { display: flex; align-items: center; }
  .contacts li:nth-child(1) { height: 31px; }
  .contacts li:nth-child(2) { height: 28px; }
  .contacts li:nth-child(3) { height: 26px; }
  .contacts li:nth-child(4) { height: 30px; }
  .contacts svg { width: 20px; height: 20px; margin-right: 25px; flex: none; }
</style>
</head>
<body>
<div class="canvas">
  <section class="card card--front">
    <div class="brand"><span class="brand__square"></span>Valdane Capital</div>
    <h1 class="person__name">Marcus Valdane</h1>
    <p class="person__title">CEO</p>
    <p class="person__address">Larkfield Court 5, 4817<br>Vista Orilla San Ramon, CA</p>
    <ul class="contacts">
      <li>
        <svg viewBox="0 0 20 20" fill="none" stroke="#fff" stroke-width="1.5"><rect x="5.5" y="1.5" width="9" height="17" rx="1.5"/><circle cx="10" cy="15.5" r="0.8" fill="#fff"/></svg>
        +1555 - 314 - 2287
      </li>
      <li>
        <svg viewBox="0 0 20 20" fill="#fff"><path d="M2 7c0-2 4-3.5 8-3.5S18 5 18 7v1.5h-4V7H6v1.5H2z"/><path d="M5 9.5h10l1.5 7h-13z"/><circle cx="10" cy="13" r="1.8" fill="#262527"/></svg>
        +1555 - 628 - 4410
      </li>
      <li>
        <svg viewBox="0 0 20 20" fill="none" stroke="#fff" stroke-width="1.5"><rect x="2" y="4.5" width="16" height="11"/><path d="M2 4.5l8 6.5 8-6.5M2 15.5l6-5M18 15.5l-6-5"/></svg>
        mvaldane@valdanecompanies.com
      </li>
      <li>
        <svg viewBox="0 0 20 20" fill="none" stroke="#fff" stroke-width="1.2"><circle cx="10" cy="10" r="8"/><ellipse cx="10" cy="10" rx="3.5" ry="8"/><path d="M2 10h16M3.5 5.5h13M3.5 14.5h13"/></svg>
        www.valdanecompanies.com
      </li>
    </ul>
  </section>

  <section class="card card--back">
    <div class="brand"><span class="brand__square"></span>Thornmere Regional Center</div>
  </section>
</div>
</body>
</html>
```